Web Site Design and Business Card design for Recruiting Company

There are three major tasks in this project:
1) I need to re-design my newly created website www.talvoro.net using the same logo but creating a totally different recruiting template that will apply better for a recruitment site. I want to use the elements of the Talvoro Network logo (which is the road junction) and red, black and gray colors throughout the website. I need someone to both design and launch the site...
2) I would also like to design a double sided business card using the same logo/colors and elements as described above
3) I would also like to have a small thumbnail logo created. As our large logo cannot be previewed easily on the Pelmwork or on Google Chrome tab images

The design should be contemporary, minimalist and slick

```html
<!DOCTYPE html>
<html lang="en">
<head>
<meta charset="utf-8">
<title>Talvoro Network — Recruiting</title>
<link href="https://fonts.googleapis.com/css2?family=Josefin+Sans:wght@600;700&family=Roboto:wght@400;500;700&family=Source+Code+Pro:wght@500&display=swap" rel="stylesheet">
<style>
:root{
  --red:#e3262b;
  --ink:#1f1f1f;
  --text:#4a4a4a;
  --muted:#8a8a8a;
  --band:#f3f1f0;
  --hero:#f0efed;
  --line:#dcdcdc;
  --white:#ffffff;
}
*{box-sizing:border-box;margin:0;padding:0}
html,body{width:1200px;height:4422px;overflow:hidden}
body{position:relative;background:var(--white);font-family:"Roboto",Arial,sans-serif;color:var(--text)}
.abs{position:absolute}
.band{position:absolute;left:0;width:1200px}
.brand{font-family:"Source Code Pro",monospace;font-weight:500;color:var(--ink);line-height:1.15;text-align:center}
.nav a{position:absolute;font-size:15px;color:var(--ink);text-decoration:none;font-weight:500}
.nav a.current{color:var(--red);border-bottom:2px solid var(--red);padding-bottom:2px}
.btn{position:absolute;background:var(--red);color:var(--white);font-size:14px;font-weight:500;display:flex;align-items:center;justify-content:center;text-transform:uppercase;box-shadow:0 8px 14px rgba(227,38,43,.28)}
.art{position:absolute;border-radius:6px}
.h-caps{font-family:"Josefin Sans",sans-serif;font-weight:700;color:var(--ink);text-transform:uppercase;letter-spacing:.5px}
.service{position:absolute;width:300px;text-align:center}
.service h3{font-size:17px;font-weight:700;color:var(--ink);margin-bottom:14px}
.service p{font-size:13.5px;line-height:22px;color:var(--text)}
.checks{position:absolute;list-style:none}
.checks li{position:relative;padding-left:44px;font-size:15px;line-height:21px;color:var(--text);height:68px}
.checks li svg{position:absolute;left:6px;top:3px}
.lead{position:absolute;font-size:16.5px;line-height:23px;color:var(--text)}
.card{position:absolute;width:299px;height:280px;background:var(--white);text-align:center;box-shadow:0 2px 8px rgba(0,0,0,.04)}
.card svg{margin-top:34px}
.card h4{font-size:17px;font-weight:500;color:var(--ink);margin:22px 0 12px}
.card p{font-size:13.5px;line-height:21px;padding:0 48px}
.partner{position:absolute;width:137px;height:127px;border:1px solid #cfcfcf;background:var(--white);display:flex;align-items:center;justify-content:center;font-weight:700;font-size:19px;color:#444}
.cand{position:absolute;left:0;height:66px;background:var(--white);display:flex;align-items:center;border-radius:2px}
.cand .av{width:46px;height:46px;border-radius:50%;margin:0 20px 0 22px}
.cand .nm{font-size:14px;color:var(--ink)}
.cand .rl{font-size:12px;color:var(--muted)}
.cand .st{position:absolute;left:210px;color:var(--red);font-size:13px;letter-spacing:1px}
.cand .bars{position:absolute;right:20px;width:44px;height:24px;border-top:3px solid #eee;border-bottom:3px solid #eee}
.cand.faded{opacity:.45}
.foot-nav{position:absolute;right:132px;top:4267px;font-size:14px;color:var(--ink)}
.foot-nav span{margin:0 8px;color:#777}
.social{position:absolute;width:26px;height:26px;border-radius:50%}
</style>
</head>
<body>

<!-- Hero -->
<section class="band" style="top:0;height:680px;background:var(--hero)">
  <svg class="abs" style="left:0;bottom:0" width="1200" height="120" viewBox="0 0 1200 120" aria-hidden="true">
    <path d="M0 70 C180 0 360 30 560 80 C760 120 900 60 1000 20 C1080 -5 1150 10 1200 0 L1200 120 L0 120Z" fill="var(--white)"/>
  </svg>
</section>

<div class="brand abs" style="left:130px;top:56px;width:222px;font-size:28px">Talvoro<br>Network</div>

<svg class="abs" style="left:870px;top:20px" width="30" height="30" viewBox="0 0 24 24" aria-hidden="true"><path d="M6.6 10.8c1.4 2.8 3.8 5.1 6.6 6.6l2.2-2.2c.3-.3.7-.4 1-.2 1.1.4 2.3.6 3.6.6.6 0 1 .4 1 1V20c0 .6-.4 1-1 1C10.6 21 3 13.4 3 4c0-.6.4-1 1-1h3.5c.6 0 1 .4 1 1 0 1.3.2 2.5.6 3.6.1.3 0 .7-.2 1z" fill="none" stroke="var(--red)" stroke-width="1.6"/></svg>
<div class="abs" style="left:910px;top:16px;width:2px;height:38px;background:var(--line)"></div>
<div class="abs" style="left:922px;top:18px;font-size:11px;color:var(--ink)">CALL US</div>
<div class="abs" style="left:922px;top:33px;font-size:18px;color:var(--ink)">+1-404-555-0172</div>
<nav class="nav">
  <a class="current" style="left:705px;top:74px">HOME</a>
  <a style="left:774px;top:74px">ABOUT US</a>
  <a style="left:877px;top:74px">SERVICES</a>
  <a style="left:975px;top:74px">CONTACT US</a>
</nav>

<h1 class="abs" style="left:130px;top:248px;font-size:35px;font-weight:500;color:var(--ink)">Hire Better, Faster!</h1>
<p class="abs" style="left:130px;top:307px;width:320px;font-size:16.5px;line-height:26px;color:var(--ink)">Talvoro Network LLC is an Atlanta based talent advisory, recruiting and staffing firm</p>
<div class="btn" style="left:132px;top:414px;width:122px;height:38px;box-shadow:none">Read More</div>
<div class="art" role="img" aria-label="Illustration of a recruiter interviewing a candidate at a table beside a large clipboard" style="left:420px;top:146px;width:690px;height:472px;background:radial-gradient(ellipse at 55% 55%,#d9d6f2 0%,#e8e4f0 45%,rgba(240,239,237,0) 75%)"></div>

<!-- Services -->
<h2 class="h-caps abs" style="left:0;width:1200px;top:746px;text-align:center;font-size:30px">Our Services</h2>
<div class="abs" style="left:585px;top:798px;width:32px;height:3px;background:#bbb"></div>

<svg class="abs" style="left:216px;top:874px" width="86" height="82" viewBox="0 0 86 82" aria-hidden="true"><rect x="3" y="8" width="80" height="54" rx="3" fill="none" stroke="#333" stroke-width="2.5"/><path d="M30 74h26M43 62v12" stroke="#333" stroke-width="2.5"/><path d="M43 4l18 7v14c0 12-8 20-18 24-10-4-18-12-18-24V11z" fill="#fff" stroke="var(--red)" stroke-width="2.5"/><path d="M35 26l6 6 11-11" fill="none" stroke="var(--red)" stroke-width="2.5"/></svg>
<svg class="abs" style="left:555px;top:872px" width="88" height="86" viewBox="0 0 88 86" aria-hidden="true"><path d="M20 6l12 18-8 8c5 12 14 21 26 26l8-8 18 12-8 14C40 76 8 44 6 14z" fill="none" stroke="#333" stroke-width="2.5"/><path d="M52 8c14 2 24 12 26 26M52 18c8 1 14 7 15 15M52 28c3 0 5 2 5 5" fill="none" stroke="var(--red)" stroke-width="2.5"/></svg>
<svg class="abs" style="left:918px;top:872px" width="74" height="86" viewBox="0 0 74 86" aria-hidden="true"><rect x="4" y="10" width="52" height="72" rx="3" fill="none" stroke="#333" stroke-width="2.5"/><rect x="12" y="18" width="36" height="12" fill="none" stroke="var(--red)" stroke-width="2.5"/><g fill="none" stroke="var(--red)" stroke-width="2"><rect x="12" y="38" width="9" height="8"/><rect x="25" y="38" width="9" height="8"/><rect x="38" y="38" width="9" height="8"/><rect x="12" y="52" width="9" height="8"/><rect x="25" y="52" width="9" height="8"/><rect x="38" y="52" width="9" height="8"/><rect x="12" y="66" width="9" height="8"/><rect x="25" y="66" width="9" height="8"/></g><path d="M62 4h6v62l-3 8-3-8z" fill="none" stroke="#333" stroke-width="2.5"/></svg>

<div class="service" style="left:108px;top:995px"><h3>Information Technology (IT)</h3><p>Project Management, Web and Application Development,Network Administration, System Engineering and Administration, Software Engineering,</p></div>
<div class="service" style="left:449px;top:995px"><h3>Telecommunications</h3><p>Project Management, Construction Management, Site Acquisition, L&amp;A Installation and Civil Work, RF Engineering and Network Design, Cell Site Integration</p></div>
<div class="service" style="left:806px;top:995px"><h3>Accounting &amp; Finance</h3><p>Financial Planning, Financial Management, Certified Public Accounting (CPA), Audit Cost Accounting, Accounts Receivable Accounts Payable, Payroll</p></div>
<div class="btn" style="left:208px;top:1174px;width:100px;height:30px;font-size:12px">Read More</div>
<div class="btn" style="left:549px;top:1174px;width:100px;height:30px;font-size:12px">Read More</div>
<div class="btn" style="left:906px;top:1174px;width:100px;height:30px;font-size:12px">Read More</div>

<!-- Candidate management -->
<section class="band" style="top:1274px;height:598px;background:var(--band)"></section>
<div class="abs" style="left:120px;top:1370px;width:446px;height:400px">
  <div class="cand faded" style="left:10px;top:0;width:426px"><div class="av" style="background:#c9c0bb"></div><div><div class="nm">Ellison</div><div class="rl">Quality Analyst</div></div><div class="st">★★★☆☆</div></div>
  <div class="cand" style="left:10px;top:75px;width:426px"><div class="av" style="background:#b79a86"></div><div><div class="nm">Ellison</div><div class="rl">Quality Analyst</div></div><div class="st">★★★★☆</div><div class="bars"></div></div>
  <div class="cand" style="left:0;top:150px;width:446px;height:78px;box-shadow:0 6px 18px rgba(0,0,0,.08)"><div class="av" style="background:#f2b51c"></div><div><div class="nm">Ellison</div><div class="rl">Quality Analyst</div></div><div class="st">★★★★★</div><div class="bars"></div></div>
  <div class="cand" style="left:10px;top:238px;width:426px"><div class="av" style="background:#5d7fa8"></div><div><div class="nm">Ellison</div><div class="rl">Quality Analyst</div></div><div class="st">★★★★☆</div><div class="bars"></div></div>
  <div class="cand faded" style="left:10px;top:313px;width:426px"><div class="av" style="background:#c9c0bb"></div><div><div class="nm">Ellison</div><div class="rl">Quality Analyst</div></div><div class="st">★★★★☆</div></div>
</div>
<h2 class="h-caps abs" style="left:618px;top:1328px;font-size:28px;line-height:40px">Effective Candidate<br>Management</h2>
<p class="lead" style="left:620px;top:1418px;width:440px">Lorem ipsum dolor sit amet&nbsp; consectetur adipiscing elit sed do eiusmod tempor incididunt ut labore et dolore magna aliqua ut enim ad minim.</p>
<ul class="checks" style="left:620px;top:1524px;width:430px">
  <li><svg width="16" height="14" viewBox="0 0 16 14"><path d="M1 7l5 5L15 1" fill="none" stroke="var(--red)" stroke-width="2.6"/></svg>Tempor incididunt ut labore et dolore magna aliqua ut enim ad minim.</li>
  <li><svg width="16" height="14" viewBox="0 0 16 14"><path d="M1 7l5 5L15 1" fill="none" stroke="var(--red)" stroke-width="2.6"/></svg>Sed ut perspiciatis unde omnis iste natus error sit voluptatem accusantium.</li>
  <li><svg width="16" height="14" viewBox="0 0 16 14"><path d="M1 7l5 5L15 1" fill="none" stroke="var(--red)" stroke-width="2.6"/></svg>At vero eos et accusamus et iusto odio dignissimos ducimus qui blanditiis.</li>
  <li><svg width="16" height="14" viewBox="0 0 16 14"><path d="M1 7l5 5L15 1" fill="none" stroke="var(--red)" stroke-width="2.6"/></svg>On the other hand, we denounce with right eous indignation&nbsp; and dislike men.</li>
</ul>
<div class="btn" style="left:632px;top:1790px;width:110px;height:32px;font-size:12px">Read More</div>

<!-- Smart interviews -->
<h2 class="h-caps abs" style="left:130px;top:1926px;font-size:28px;line-height:40px">Smart Interviews for<br>Smarter People</h2>
<p class="lead" style="left:130px;top:2026px;width:440px">Lorem ipsum dolor sit amet&nbsp; consectetur adipiscing elit sed do eiusmod tempor incididunt ut labore et dolore magna aliqua ut enim ad minim.</p>
<ul class="checks" style="left:130px;top:2137px;width:430px">
  <li><svg width="16" height="14" viewBox="0 0 16 14"><path d="M1 7l5 5L15 1" fill="none" stroke="var(--red)" stroke-width="2.6"/></svg>Tempor incididunt ut labore et dolore magna aliqua ut enim ad minim.</li>
  <li><svg width="16" height="14" viewBox="0 0 16 14"><path d="M1 7l5 5L15 1" fill="none" stroke="var(--red)" stroke-width="2.6"/></svg>Sed ut perspiciatis unde omnis iste natus error sit voluptatem accusantium.</li>
  <li><svg width="16" height="14" viewBox="0 0 16 14"><path d="M1 7l5 5L15 1" fill="none" stroke="var(--red)" stroke-width="2.6"/></svg>At vero eos et accusamus et iusto odio dignissimos ducimus qui blanditiis.</li>
  <li><svg width="16" height="14" viewBox="0 0 16 14"><path d="M1 7l5 5L15 1" fill="none" stroke="var(--red)" stroke-width="2.6"/></svg>On the other hand, we denounce with right eous indignation&nbsp; and dislike men.</li>
</ul>
<div class="art" role="img" aria-label="Illustration of three colleagues holding an interview at a desk under a hanging lamp, with a potted plant" style="left:566px;top:1872px;width:534px;height:600px;border-radius:0;background:linear-gradient(180deg,#ffffff 0%,#f4f5fa 40%,#e6e7f1 100%)"></div>

<!-- Customers -->
<section class="band" style="top:2459px;height:537px;background:var(--band)"></section>
<h2 class="abs" style="left:0;width:1200px;top:2558px;text-align:center;font-family:'Josefin Sans',sans-serif;font-weight:600;font-size:27px;color:var(--ink)">Our customers love us, and we know you will too.</h2>
<div class="card" style="left:132px;top:2648px"><svg width="60" height="82" viewBox="0 0 60 82" aria-hidden="true"><path d="M4 4h38l14 14v60H4z" fill="none" stroke="#333" stroke-width="2.5"/><g stroke="var(--red)" stroke-width="2.5" fill="none"><rect x="13" y="28" width="6" height="6"/><rect x="13" y="44" width="6" height="6"/><rect x="13" y="60" width="6" height="6"/><path d="M25 31h22M25 47h22M25 63h22"/></g></svg><h4>Unlimited jobs &amp; users</h4><p>Lorem ipsum dolor sit amet con se ctetur adipiscing elit sed do eiusmod tempor incid.</p></div>
<div class="card" style="left:451px;top:2648px"><svg width="80" height="82" viewBox="0 0 80 82" aria-hidden="true"><path d="M6 4h36l12 12v34M40 74H6V4" fill="none" stroke="#333" stroke-width="2.5"/><path d="M14 26h28M14 36h28M14 46h18" stroke="#333" stroke-width="2.5"/><circle cx="58" cy="62" r="15" fill="none" stroke="var(--red)" stroke-width="2.5"/><path d="M58 54v8h6" fill="none" stroke="var(--red)" stroke-width="2.5"/></svg><h4>Get up and running fast.</h4><p>Lorem ipsum dolor sit amet con se ctetur adipiscing elit sed do eiusmod tempor incid.</p></div>
<div class="card" style="left:771px;top:2648px"><svg width="76" height="82" viewBox="0 0 76 82" aria-hidden="true"><rect x="6" y="22" width="64" height="42" fill="none" stroke="#333" stroke-width="2.5"/><path d="M2 72h72M14 64v8M62 64v8" stroke="#333" stroke-width="2.5"/><circle cx="38" cy="22" r="10" fill="#fff" stroke="var(--red)" stroke-width="2.5"/><circle cx="38" cy="22" r="3.5" fill="none" stroke="var(--red)" stroke-width="2"/><path d="M22 50h32" stroke="#333" stroke-width="2" stroke-dasharray="3 3"/></svg><h4>Highly customizable.</h4><p>Lorem ipsum dolor sit amet con se ctetur adipiscing elit sed do eiusmod tempor incid.</p></div>

<!-- Partners -->
<div class="partner" style="left:151px;top:3068px">Quorvel</div>
<div class="partner" style="left:302px;top:3111px">Nesterra</div>
<div class="partner" style="left:453px;top:3068px">Kindwell</div>
<div class="partner" style="left:151px;top:3212px">Haxlo</div>
<div class="partner" style="left:302px;top:3255px">Ventiro</div>
<div class="partner" style="left:453px;top:3212px">Brantis</div>
<div class="abs" style="left:661px;top:3102px;font-size:15px;font-weight:700;color:var(--ink)">PARTNERS</div>
<h3 class="abs" style="left:661px;top:3138px;width:400px;font-size:22px;font-weight:400;line-height:30px;color:var(--ink)">Bring the power of our recruiting solution to your customers.</h3>
<p class="lead" style="left:661px;top:3220px;width:400px;font-size:15.5px">Lorem ipsum dolor sit amet con se ctetur adipiscing elit sed do eiusmod tempor incid.</p>
<a class="abs" style="left:663px;top:3291px;font-size:13.5px;color:var(--red);text-decoration:underline">Become a partner today</a>

<!-- Call to action + footer -->
<section class="band" style="top:3460px;height:962px;background:var(--band)">
  <svg class="abs" style="left:0;top:540px" width="1200" height="422" viewBox="0 0 1200 422" aria-hidden="true">
    <path d="M0 40 C150 10 300 70 420 110 C560 150 700 60 880 40 C1000 28 1100 -10 1200 0 L1200 422 L0 422Z" fill="#e4e3e3"/>
  </svg>
</section>
<div class="art" role="img" aria-label="Illustration of a team of three collaborating around a table with a laptop and chat bubbles" style="left:17px;top:3528px;width:670px;height:404px;background:radial-gradient(ellipse at 50% 60%,#dcdbe8 0%,#ebeaf0 45%,rgba(243,241,240,0) 78%)"></div>
<h2 class="h-caps abs" style="left:747px;top:3586px;font-size:29px;line-height:40px">Start Making Great<br>Hires Today.</h2>
<p class="lead" style="left:747px;top:3680px;width:330px;font-size:16.5px;line-height:26px">Lorem ipsum dolor sit amet&nbsp; consectetur adipiscing elit sed do eiusmod tempor incididunt ut labore et dolore.</p>
<div class="btn" style="left:752px;top:3795px;width:173px;height:52px;font-size:17px">Get Started</div>

<div class="brand abs" style="left:129px;top:4108px;width:300px;font-size:36px">Talvoro<br>Network</div>
<div class="abs" style="left:894px;top:4215px;font-size:14px;color:var(--ink)">FOLLOW</div>
<div class="social" role="img" aria-label="Fenlyt" style="left:970px;top:4209px;background:#2f62c8"></div>
<div class="social" role="img" aria-label="Chirpo" style="left:1004px;top:4209px;background:#3c9be4"></div>
<div class="social" role="img" aria-label="Pelmwork" style="left:1038px;top:4209px;background:#263a7a"></div>
<div class="foot-nav">HOME<span>|</span>ABOUT US<span>|</span>SERVICES<span>|</span>CONTACT US</div>
<div class="abs" style="left:130px;top:4320px;width:940px;height:1px;background:#c8c8c8"></div>
<svg class="abs" style="left:132px;top:4352px" width="34" height="34" viewBox="0 0 34 34" aria-hidden="true"><circle cx="17" cy="17" r="17" fill="var(--red)"/><path d="M12 9l3 5-2 2c1 3 3 5 6 6l2-2 5 3-2 3c-7 0-14-7-14-14z" fill="#fff"/></svg>
<div class="abs" style="left:180px;top:4359px;font-size:17px;color:var(--ink)">+1-404-555-0172</div>
<svg class="abs" style="left:355px;top:4352px" width="34" height="34" viewBox="0 0 34 34" aria-hidden="true"><circle cx="17" cy="17" r="17" fill="var(--red)"/><rect x="9" y="11" width="16" height="12" fill="#fff"/><path d="M9 11l8 7 8-7" fill="none" stroke="var(--red)" stroke-width="1.6"/></svg>
<div class="abs" style="left:396px;top:4359px;font-size:17px;color:var(--ink)">info@talvoro.net</div>
<div class="abs" style="right:132px;top:4363px;font-size:11px;color:var(--ink)">Copyright © 2019 All Rights Reserved</div>

</body>
</html>
```